Tech business card design

We need an amazing business card design for our new business 'Pexla' a marketing tech startup based in Sydney, Australia. We provide an online marketplace for businesses to search and buy advertising media, connect with service providers and learn more about marketing. We wish to communicate 'cool tech', reliability and professionalism and design based around our logo.

Target Market(s)

Business Owners

Contact Information for Business Card

Name
Position
Email Address
Website
Phone Number

Font styles to use
Other font styles liked:
• Avenir & Avenir Next

Colors

Designer to choose colors to be used in the design.

```html
<!DOCTYPE html>
<html lang="en">
<head>
<meta charset="utf-8">
<title>Pexla Business Card</title>
<link rel="stylesheet" href="https://fonts.googleapis.com/css2?family=Roboto:wght@500;700&family=Work+Sans:wght@400&display=swap">
<style>
  :root {
    --navy: #13143f;
    --white: #ffffff;
    --ink-soft: #4a4a55;
    --rule: #1d1f4d;
    --stage: #c9c9c9;
  }
  * { margin: 0; padding: 0; box-sizing: border-box; }
  html, body { width: 1200px; height: 930px; overflow: hidden; }
  body {
    background: var(--stage);
    position: relative;
    font-family: "Work Sans", sans-serif;
  }
  .card {
    position: absolute;
    width: 560px;
    height: 320px;
    border-radius: 24px;
    overflow: hidden;
  }
  .card-front {
    left: 60px; top: 110px;
    background: var(--navy);
    display: flex; align-items: center; justify-content: center;
  }
  .card-front .brand-name {
    font-family: "Roboto", sans-serif;
    font-weight: 700;
    font-size: 92px;
    color: var(--white);
    letter-spacing: -1px;
  }
  .card-back {
    left: 580px; top: 480px;
    background: var(--white);
  }
  .card-back .brand-name {
    position: absolute; left: 34px; top: 74px;
    font-family: "Roboto", sans-serif;
    font-weight: 700;
    font-size: 66px;
    color: var(--navy);
    letter-spacing: -1px;
  }
  .holder {
    position: absolute; right: 34px; top: 34px;
    text-align: right;
  }
  .holder-name {
    font-family: "Roboto", sans-serif;
    font-weight: 700; font-size: 22px; color: var(--navy);
  }
  .holder-role { font-size: 12px; color: var(--ink-soft); margin-top: 2px; }
  .rule { position: absolute; height: 1px; background: var(--rule); }
  .rule-top { right: 34px; top: 94px; width: 250px; }
  .rule-bottom { left: 34px; top: 206px; width: 250px; }
  .address {
    position: absolute; right: 34px; top: 108px;
    text-align: right; font-size: 14px; line-height: 1.4; color: var(--ink-soft);
  }
  .contacts {
    position: absolute; left: 34px; top: 218px;
    list-style: none; font-size: 15px; line-height: 1.35; color: var(--ink-soft);
  }
  .contacts li { display: flex; align-items: center; gap: 10px; }
  .contacts svg { width: 11px; height: 11px; fill: var(--navy); flex: none; }
  .band { position: absolute; left: 0; bottom: 0; width: 560px; height: 140px; }
</style>
</head>
<body>
  <div class="card card-front">
    <span class="brand-name">Pexla</span>
  </div>

  <div class="card card-back">
    <span class="brand-name">Pexla</span>

    <div class="holder">
      <div class="holder-name">Daniel Arkwright</div>
      <div class="holder-role">Director</div>
    </div>
    <div class="rule rule-top"></div>

    <div class="address">218 Kessel Lane<br>Marrick, NSW 2150</div>

    <div class="rule rule-bottom"></div>
    <ul class="contacts">
      <li><svg viewBox="0 0 12 12"><path d="M2.5 0.5l2 2.6-1 1.2c.7 1.6 1.9 2.9 3.6 3.7l1.2-1 2.6 1.9-1 2.2C5.6 11 1 6.4 0.6 1.6z"/></svg>+61 2 9481 3307</li>
      <li><svg viewBox="0 0 12 12"><path d="M0 2h12v8H0zM1 3v.4l5 3.2 5-3.2V3zm0 1.6V9h10V4.6L6 7.8z"/></svg>info@pexla.com</li>
      <li><svg viewBox="0 0 12 12"><circle cx="6" cy="6" r="6"/></svg>www.pexla.com</li>
    </ul>

    <svg class="band" viewBox="0 0 560 140" aria-hidden="true">
      <path d="M0 128 L400 128 L404 62 L560 62 L560 140 L0 140 Z" fill="var(--navy)"/>
      <path d="M392 128 L396 62 L400 62 L396 128 Z" fill="var(--navy)"/>
    </svg>
  </div>
</body>
</html>
```